I have a business that exists already (Linden Conservatory of Music) that we offer music lessons to all instruments. I recently opened a smaller version called CHORDS by Linden that will only teach piano lessons. What I'm looking for now is a 3 page Website on word press. After I choose the design I like I want to be able to take over the website and bring it to our hosting company. We want full control of it and our team will take over. The reason I'm doing this is to have other visions and ideas from others. The first page will be about the company and our message/vision. Second page about the piano lessons. The third will be about franchising this concept "Chords by Linden" Attached are 3 Logos . Please refer to our existing website www.lindenmusicconservatory.example to look at our piano page and franchising page. Please feel free to message me if you need more info. Thanks
Please note I do not want the new website (Chords by Linden) To look like the other Website (Linden Conservatory of Music) Fresh new look. I do not want the colours red or using the Red logo. I only provided it so that you have an Idea of What the other business looks like and that you can take the piano content and franchise content off of it. Chords by Linden is smaller concept and only piano lessons.
Thanks
Only Piano lessons for all students
3 page

```html
<!DOCTYPE html>
<html lang="en">
<head>
<meta charset="utf-8">
<title>CHORDS by Linden — Piano Lessons</title>
<link rel="stylesheet" href="https://fonts.googleapis.com/css2?family=Lora:ital,wght@0,400;0,700;1,400&family=Yesteryear&family=Montserrat:wght@400&display=swap">
<style>
  :root {
    --teal: #5bc8bb;
    --black: #000;
    --white: #fff;
    --ink: #222;
    --text: #333;
    --paper: #f0efeb;
    --hero-dark: #2a1610;
    --hero-mid: #6b3a22;
    --hero-warm: #a8683f;
  }
  * { box-sizing: border-box; margin: 0; padding: 0; }
  html, body { width: 1200px; height: 2845px; overflow: hidden; }
  body { position: relative; background: var(--white); font-family: "Lora", Georgia, serif; color: var(--text); }
  .abs { position: absolute; }

  .site-header { left: 0; top: 0; width: 1200px; height: 88px; background: var(--black); }
  .brand { left: 143px; top: 22px; color: var(--white); font-size: 26px; font-family: "Lora", serif; display: flex; align-items: center; gap: 10px; }
  .brand-dot { width: 14px; height: 14px; border-radius: 50%; background: var(--white); }
  .nav a { position: absolute; top: 45px; color: var(--white); text-decoration: none; font-size: 14px; text-transform: uppercase; letter-spacing: .2px; white-space: nowrap; }
  .nav a.active { color: var(--teal); font-weight: 700; }

  .hero { left: 0; top: 88px; width: 1200px; height: 550px;
    background: radial-gradient(ellipse at 55% 55%, var(--hero-warm) 0%, var(--hero-mid) 40%, var(--hero-dark) 85%); }
  .hero-title { left: 0; width: 1200px; text-align: center; font-family: "Yesteryear", cursive; color: var(--white); text-shadow: 0 2px 4px rgba(0,0,0,.5); }
  .btn { background: var(--teal); color: var(--white); font-family: "Lora", serif; font-weight: 700; text-transform: uppercase; display: flex; align-items: center; justify-content: center; text-decoration: none; font-size: 13px; letter-spacing: .3px; }
  .btn.abs, .abs > .btn.placed { position: absolute; }

  .intro-band { left: 0; top: 638px; width: 1200px; height: 505px; background: var(--paper); }
  .intro-photo { left: 141px; top: 590px; width: 437px; height: 422px; background: linear-gradient(135deg, #d9cfc6, #7d716a 55%, #1c1a1b); }
  .intro-card { left: 578px; top: 590px; width: 480px; height: 422px; background: var(--white); text-align: center; padding: 40px 46px 0; }
  .intro-card h2 { font-weight: 400; font-size: 35px; color: var(--ink); margin-bottom: 18px; }
  .intro-card p { font-size: 13px; line-height: 23px; margin-bottom: 5px; color: var(--text); }

  h2.section-title { font-weight: 400; font-size: 35px; color: var(--ink); line-height: 1.2; }
  .vision-block { left: 143px; top: 1250px; width: 492px; }
  .vision-block h2 { margin-bottom: 9px; }
  .body-copy { font-size: 12.6px; line-height: 25.4px; color: var(--text); }
  .body-copy p { margin-bottom: 7px; }
  .vision-block .btn { width: 169px; height: 35px; margin-top: 22px; margin-left: -2px; }

  .teal-block { background: var(--teal); }
  .frame-line { border: 1.5px solid var(--white); }
  .vision-photo { background: linear-gradient(135deg, #f4ece4, #e8b9a4 50%, #d7a9b7); }
  .programs-photo { background: linear-gradient(135deg, #efe9e3, #c9a58c 50%, #2a2c3a); }

  .programs-list { left: 584px; top: 1756px; width: 470px; list-style: none; font-size: 14.5px; line-height: 22.6px; color: var(--text); }
  .programs-list li { position: relative; padding-left: 18px; margin-bottom: 9px; }
  .programs-list svg { position: absolute; left: 0; top: 6px; }

  .quote-card { left: 141px; top: 2147px; width: 917px; height: 212px; background: var(--white); border-radius: 20px; box-shadow: 0 2px 14px rgba(0,0,0,.1); }
  .quote-mark { left: 222px; top: 2130px; font-family: "Lora", serif; font-size: 200px; color: #ececec; line-height: 1; }
  .quote-text { left: 141px; width: 917px; top: 2196px; text-align: center; font-style: italic; font-size: 22px; line-height: 38px; color: var(--ink); padding: 0 140px 0 150px; }
  .quote-author { left: 141px; width: 917px; top: 2284px; text-align: center; color: var(--teal); font-weight: 700; font-size: 17px; letter-spacing: .5px; }

  .franchise-title { left: 0; width: 1200px; top: 2428px; text-align: center; font-size: 46px; font-weight: 400; color: var(--ink); }
  .franchise-sub { left: 0; width: 1200px; top: 2496px; text-align: center; font-size: 21px; text-transform: uppercase; color: var(--text); }

  .site-footer { left: 0; top: 2646px; width: 1200px; height: 150px; background: var(--black); color: var(--white); }
  .contact-item { position: absolute; top: 44px; display: flex; align-items: center; gap: 10px; }
  .contact-item .label { font-size: 14px; }
  .contact-item .big { font-size: 19px; }
  .contact-item .small { font-size: 12.5px; line-height: 18px; color: var(--white); }
  .footer-divider { position: absolute; top: 54px; width: 1px; height: 30px; background: #555; }

  .legal-bar { left: 0; top: 2796px; width: 1200px; height: 49px; background: var(--teal); }
  .copyright { position: absolute; left: 142px; top: 16px; font-family: "Montserrat", sans-serif; font-size: 12px; color: var(--white); }
  .social { position: absolute; top: 12px; width: 24px; height: 24px; border: 1.5px solid var(--white); border-radius: 50%; }
</style>
</head>
<body>

<header class="abs site-header">
  <div class="abs brand"><span class="brand-dot"></span>CHORDS by Linden</div>
  <nav class="nav">
    <a class="active" style="left:616px">Home</a>
    <a style="left:693px">Piano Lessons</a>
    <a style="left:837px">Franchising</a>
    <a style="left:966px">Contact Us</a>
  </nav>
</header>

<section class="abs hero" role="img" aria-label="Close-up photo of an upright piano keyboard in warm brown light"></section>
<div class="abs hero-title" style="top:326px;font-size:44px;">We Provide Piano Lessons</div>
<div class="abs hero-title" style="top:387px;font-size:33px;">For All Students</div>
<a class="btn abs" style="left:501px;top:444px;width:198px;height:40px;font-size:15px;font-weight:400;">Contact Us Today</a>

<section class="abs intro-band"></section>
<div class="abs intro-photo" role="img" aria-label="Photo of hands playing piano keys"></div>
<div class="abs intro-card">
  <h2>Playing The Piano</h2>
  <p>When you think of a piano, you probably envision black and white keys but the piano is more than those harmonious sounds created by the player.</p>
  <p>The versatility and the musicianship instilled into the player from those keys is the true magic that comes from playing piano! Starting from the grassroots, experience different methods and styles of playing piano. To mark the milestones of progression, engage in one of Linden’s many unique performance opportunities like annual festival competitions, recitals or our examinations (Linden &amp; NBM). Penultimately, at the end of the journey, join our elite teaching program to bring the same joy of learning the piano to another student.</p>
</div>
<svg class="abs" style="left:571px;top:1043px" width="58" height="58" viewBox="0 0 58 58" aria-hidden="true">
  <rect x="12" y="12" width="34" height="34" transform="rotate(45 29 29)" fill="none" stroke="#d4d2cc" stroke-width="1.5"/>
  <path d="M29 22v13M24 30l5 5 5-5" fill="none" stroke="#c4c2bc" stroke-width="1.5"/>
</svg>

<div class="abs vision-block">
  <h2 class="section-title">Our Vision</h2>
  <div class="body-copy">
    <p>Lorem ipsum dolor sit amet, consectetur adipiscing elit. In hendrerit, odio utrtyy semper consequat, justo dui convallis ligula, ac congue felis ipsum sed felis. Cura volutpat leo faucibus magna elementum ultrices.</p>
    <p>Cras eleifend faucibus lacus convallis elementum. Phasellus vitae lobortis donece in risus sit amet enim eleifend semper sed id ipsum. Ut ac placerat nisl pellentesq venenatis ligula eget turpis aliquam ornare. Vivamus tincidunt tellus at rutrum fd aliquam. Etiam ullamcorper consequat felis vitae posuere. Nunc nec facilisis nuni, at dignissim augue. Sed sed orci felis. Aliquam quis auctor ipsum.</p>
  </div>
  <a class="btn">Contact Us Today</a>
</div>

<div class="abs teal-block" style="left:741px;top:1222px;width:317px;height:318px;"></div>
<div class="abs frame-line" style="left:759px;top:1240px;width:281px;height:282px;"></div>
<div class="abs vision-photo" style="left:678px;top:1283px;width:318px;height:316px;" role="img" aria-label="Photo of a teacher with two children at a keyboard"></div>

<div class="abs teal-block" style="left:141px;top:1667px;width:317px;height:317px;"></div>
<div class="abs frame-line" style="left:159px;top:1685px;width:299px;height:299px;border-right:none;border-bottom:none;"></div>
<div class="abs programs-photo" style="left:204px;top:1728px;width:317px;height:316px;" role="img" aria-label="Photo of a teacher and student playing piano together"></div>

<h2 class="abs section-title" style="left:576px;top:1660px;font-size:31px;line-height:40px;">Our Programs Also Provide Students<br>The Opportunity To</h2>
<ul class="abs programs-list">
  <li><svg width="12" height="12" viewBox="0 0 12 12"><circle cx="6" cy="6" r="5" fill="none" stroke="#555"/><path d="M3.5 6l2 2 4-4.5" fill="none" stroke="#555"/></svg>Participate in large-scale performances.</li>
  <li><svg width="12" height="12" viewBox="0 0 12 12"><circle cx="6" cy="6" r="5" fill="none" stroke="#555"/><path d="M3.5 6l2 2 4-4.5" fill="none" stroke="#555"/></svg>Perform at Linden’s many community events on a regular basis.</li>
  <li><svg width="12" height="12" viewBox="0 0 12 12"><circle cx="6" cy="6" r="5" fill="none" stroke="#555"/><path d="M3.5 6l2 2 4-4.5" fill="none" stroke="#555"/></svg>Access the GTA’s coolest Broadcast stage</li>
  <li><svg width="12" height="12" viewBox="0 0 12 12"><circle cx="6" cy="6" r="5" fill="none" stroke="#555"/><path d="M3.5 6l2 2 4-4.5" fill="none" stroke="#555"/></svg>Attend Clinics, Masterclasses, and Jam Nights</li>
  <li><svg width="12" height="12" viewBox="0 0 12 12"><circle cx="6" cy="6" r="5" fill="none" stroke="#555"/><path d="M3.5 6l2 2 4-4.5" fill="none" stroke="#555"/></svg>Access the Linden Rocks band program. Linden’s Band Program empowers and electrifies students to come together, create music and confidently hit the stage with their own band identity while having fun and honing their instrument.</li>
  <li><svg width="12" height="12" viewBox="0 0 12 12"><circle cx="6" cy="6" r="5" fill="none" stroke="#555"/><path d="M3.5 6l2 2 4-4.5" fill="none" stroke="#555"/></svg>Register in our elite teaching program to learn how to pass on the magic and passion of playing the piano to students.</li>
</ul>
<a class="btn abs" style="left:575px;top:2041px;width:169px;height:35px;">Contact Us Today</a>

<div class="abs quote-card"></div>
<div class="abs quote-mark" aria-hidden="true">“</div>
<div class="abs quote-text">“Life is like a piano. What you get out of it depends on how you play it.”</div>
<div class="abs quote-author">MARTIN ASHBY</div>

<h2 class="abs franchise-title">Franchise Opportunities</h2>
<div class="abs franchise-sub">Be part of the Linden Academy family</div>
<a class="btn abs" style="left:530px;top:2540px;width:140px;height:35px;">Know More</a>

<footer class="abs site-footer">
  <div class="contact-item" style="left:190px;">
    <svg width="40" height="40" viewBox="0 0 40 40"><circle cx="20" cy="20" r="18" fill="none" stroke="#fff" stroke-width="2"/><path d="M14 12c-2 2-1 7 4 12s10 6 12 4l-3-4-3 2c-2-1-5-4-6-6l2-3z" fill="#fff"/></svg>
    <div><div class="label">Call Us Now</div><div class="big">1-800-555-0142</div></div>
  </div>
  <div class="footer-divider" style="left:442px;"></div>
  <div class="contact-item" style="left:478px;">
    <svg width="40" height="40" viewBox="0 0 40 40"><circle cx="20" cy="20" r="18" fill="none" stroke="#fff" stroke-width="2"/><path d="M20 10a7 7 0 0 0-7 7c0 5 7 13 7 13s7-8 7-13a7 7 0 0 0-7-7z" fill="none" stroke="#fff" stroke-width="2"/><circle cx="20" cy="17" r="2.5" fill="#fff"/></svg>
    <div><div class="label" style="font-weight:700;font-size:13px;">CHORDS LINDEN</div><div class="small">123, Building Name, Street Name<br>State, City XY 123456</div></div>
  </div>
  <div class="footer-divider" style="left:757px;"></div>
  <div class="contact-item" style="left:814px;">
    <svg width="40" height="40" viewBox="0 0 40 40"><circle cx="20" cy="20" r="18" fill="none" stroke="#fff" stroke-width="2"/><rect x="12" y="14" width="16" height="12" rx="1.5" fill="#fff"/><path d="M12 15l8 6 8-6" fill="none" stroke="#000" stroke-width="1.5"/></svg>
    <div><div class="label">Email Us:</div><div class="small">inquiry@chordslinden.example</div></div>
  </div>
</footer>

<div class="abs legal-bar">
  <div class="copyright">Copyright © 2020 CHORDS LINDEN. All Rights Reserved.</div>
  <span class="social" style="left:940px;" aria-label="Social link"></span>
  <span class="social" style="left:971px;" aria-label="Social link"></span>
  <span class="social" style="left:1002px;" aria-label="Social link"></span>
  <span class="social" style="left:1033px;" aria-label="Social link"></span>
</div>

</body>
</html>
```